Looking to Redesign Brevonix.com website

You guys did one of the brochures for brevonix.com and I would like to see if we can go ahead and get an estimate for a redesigned web site for the company. We currently have a couple of pages on brevonix.com which are very much a starter type site.

The new design will need to reflect some of the things discussed in the brochure. It will have flash. Needs to be designed for simple hosting using cpanels.

The site needs to have between 12 and 15 pages with flash pages to move through features. Integrated with twitter like it is now, and contact forms delivered from our CRM along with other interactive features such as subscription to newsletter, etc...

I don't have lots of details on how to proceed yet, but here are some competitor sites:

Can we take a look at potential costs involved in the redo of the site as vague as my description above can permit.

Target Market(s)

Business to Business

Number of Pages Required

5+ page

Font styles to use
Sans Serif

Requirements
Must have
• Must have professional feel. Similar to brochure. and logo.
• Include our story in the discussion.
• embedded links to our CRM for popup contact forms.
• Logo files and 2 types of brochures uploaded.
• Important to keep color scheme
Nice to have
• Flash and some movement
Should not have
• Not sure yet

```html
<!DOCTYPE html>
<html lang="en">
<head>
<meta charset="utf-8">
<title>Brevonix Universal Communication</title>
<link rel="stylesheet" href="https://fonts.googleapis.com/css2?family=Arimo:wght@400;700&family=Open+Sans:wght@400;600&family=Oswald:wght@500;700&family=Roboto+Condensed:wght@400;700&display=swap">
<style>
:root{
  --red:#b00000;
  --red-deep:#8f0000;
  --red-tile:#9a0000;
  --black:#000;
  --ink:#222;
  --muted:#777;
  --paper:#fff;
  --mist:#ececec;
  --social:#1a7fd0;
  --photo-dark:#0c1a2e;
  --photo-mid:#3a5a7c;
}
*{box-sizing:border-box;margin:0;padding:0}
html,body{width:1200px;height:2439px;overflow:hidden}
body{position:relative;background:var(--paper);font-family:"Open Sans",Arial,sans-serif;color:var(--ink)}
.btn-outline{position:absolute;display:flex;align-items:center;justify-content:center;border:2px solid var(--red);border-radius:24px;color:var(--red);font-family:"Arimo",Arial,sans-serif;font-size:16px;letter-spacing:.5px}
.notch{position:absolute;left:570px;width:60px;height:30px}

/* header */
.site-header{position:absolute;left:0;top:0;width:1200px;height:107px;background:var(--paper)}
.brand{position:absolute;left:133px;top:32px;display:flex;align-items:center;gap:10px}
.brand-dot{width:40px;height:40px;border-radius:50%;background:var(--red)}
.brand-name{font-family:"Arimo",Arial,sans-serif;font-weight:700;font-size:24px;color:var(--red)}
.main-nav{position:absolute;left:338px;top:47px;display:flex;font-family:"Roboto Condensed",Arial,sans-serif;font-size:12px;color:var(--ink);white-space:nowrap}
.main-nav span{padding:9px 11px;margin-right:4px}
.main-nav .active{border:1.5px solid var(--red);border-radius:20px;padding:8px 16px}
.social-top{position:absolute;top:-6px;left:951px;display:flex;gap:2px}
.social-top i{width:32px;height:32px;border-radius:50%;background:var(--social);display:block}

/* hero */
.hero{position:absolute;left:0;top:107px;width:1200px;height:514px;background:radial-gradient(ellipse at 50% 40%,#c0101a 0%,#7a0008 45%,#2a0003 80%,#100001 100%)}
.hero-mark{position:absolute;left:0;width:1200px;top:120px;display:flex;justify-content:center;align-items:center;gap:10px}
.hero-mark i{width:56px;height:56px;border-radius:50%;background:rgba(255,255,255,.55);display:block}
.hero-mark b{font-family:"Arimo",Arial,sans-serif;font-weight:700;font-size:26px;color:rgba(255,255,255,.75)}
.hero-title{position:absolute;top:218px;width:1200px;text-align:center;font-family:"Oswald",Arial,sans-serif;font-weight:700;font-size:50px;color:#fff;letter-spacing:.5px;line-height:70px}
.hero-sub{position:absolute;top:290px;width:1200px;text-align:center;font-family:"Arimo",Arial,sans-serif;font-size:21px;color:#fff;letter-spacing:.5px}
.hero .btn-outline{left:512px;top:343px;width:166px;height:51px;border-color:#fff;color:#fff;font-size:17px}

/* about */
.about{position:absolute;left:0;top:621px;width:1200px;height:322px;background:var(--mist)}
.section-title{font-family:"Arimo",Arial,sans-serif;font-size:32px;color:var(--red);font-weight:400}
.about .section-title{position:absolute;top:80px;width:1200px;text-align:center}
.about p{position:absolute;left:200px;width:800px;top:140px;text-align:center;font-size:13.5px;line-height:25px;color:var(--muted)}
.about .btn-outline{left:532px;top:241px;width:136px;height:42px}

/* why */
.why{position:absolute;left:0;top:943px;width:1200px;height:551px;background:var(--paper)}
.why-photo{position:absolute;left:0;top:0;width:1200px;height:551px}
.why .section-title{position:absolute;left:143px;top:24px;font-size:31px}
.why-kicker{position:absolute;left:148px;top:67px;font-family:"Arimo",Arial,sans-serif;font-size:13px;color:var(--ink)}
.why-copy{position:absolute;left:148px;top:98px;width:450px;font-size:11.5px;line-height:20px;color:#555}
.why-copy p{margin-bottom:18px}
.why-list{position:absolute;left:148px;top:228px;width:450px;list-style:none}
.why-list li{position:relative;padding-left:27px;font-size:13px;font-weight:600;line-height:20px;color:var(--ink);margin-bottom:20px}
.why-list svg{position:absolute;left:0;top:4px}
.why .btn-outline{left:156px;top:472px;width:137px;height:42px}

/* benefits */
.benefits{position:absolute;left:0;top:1494px;width:1200px;height:464px;background:radial-gradient(ellipse at 50% 50%,#c00000 0%,var(--red) 60%,#a00000 100%)}
.benefits .section-title{position:absolute;top:50px;width:1200px;text-align:center;color:#fff;font-size:32px}
.benefits-sub{position:absolute;top:93px;width:1200px;text-align:center;font-family:"Arimo",Arial,sans-serif;font-size:13px;color:#fff;letter-spacing:.3px}
.benefit{position:absolute;width:299px;height:126px;background:var(--red-tile);padding:22px 24px 0 75px;color:#fff}
.benefit.featured{background:var(--black)}
.benefit svg{position:absolute;left:36px;top:24px}
.benefit h3{font-family:"Arimo",Arial,sans-serif;font-weight:400;font-size:20px;margin-bottom:12px}
.benefit p{font-family:"Arimo",Arial,sans-serif;font-size:11px;line-height:19px;text-transform:uppercase}
.dashes{position:absolute;top:1431px;left:568px;display:flex;gap:10px}
.dashes i{display:block;width:16px;height:3px;background:#fff}

/* newsletter */
.newsletter{position:absolute;left:0;top:1958px;width:1200px;height:192px;background:var(--mist)}
.newsletter h2{position:absolute;left:245px;top:78px;font-family:"Arimo",Arial,sans-serif;font-weight:400;font-size:20px;line-height:24px;color:var(--red);white-space:nowrap}
.newsletter .rule{position:absolute;left:245px;top:117px;width:158px;height:1px;background:var(--red)}
.newsletter small{position:absolute;left:407px;top:110px;font-family:"Arimo",Arial,sans-serif;font-size:12px;color:var(--red)}
.email-field{position:absolute;left:541px;top:78px;width:292px;height:36px;border-radius:18px;background:#fff;padding:0 20px;display:flex;align-items:center;justify-content:space-between;font-size:12px;color:#aaa}
.subscribe{position:absolute;left:844px;top:78px;width:119px;height:36px;border-radius:18px;background:var(--red);color:#fff;font-family:"Arimo",Arial,sans-serif;font-size:15px;display:flex;align-items:center;justify-content:center}

/* footer */
.site-footer{position:absolute;left:0;top:2150px;width:1200px;height:289px;background:var(--black);color:#fff}
.foot-brand{position:absolute;left:208px;top:36px;display:flex;align-items:center;gap:10px}
.foot-brand i{width:40px;height:40px;border-radius:50%;background:#fff;display:block}
.foot-brand b{font-family:"Arimo",Arial,sans-serif;font-weight:700;font-size:22px;color:#fff}
.foot-about{position:absolute;left:202px;top:110px;width:210px;font-family:"Arimo",Arial,sans-serif;font-size:10.5px;line-height:20px}
.foot-col h4{font-family:"Arimo",Arial,sans-serif;font-weight:400;font-size:13px;color:var(--red);margin-bottom:14px}
.foot-col{position:absolute;top:41px;font-family:"Arimo",Arial,sans-serif;font-size:10px;line-height:24px}
.quick{left:462px}
.quick ul{list-style:none;padding-left:4px}
.testimonial{left:631px;width:200px;line-height:19px;font-size:10px}
.testimonial cite{display:block;color:var(--red);font-style:normal;margin-top:8px;font-size:11px}
.contact{left:896px}
.contact li{list-style:none;display:flex;align-items:center;gap:16px;height:24px}
.contact li i{width:8px;height:8px;border-radius:50%;background:#fff;display:block}
.foot-social{position:absolute;left:896px;top:197px;display:flex;gap:14px}
.foot-social i{width:9px;height:9px;border-radius:50%;background:#fff;display:block}
.copyright{position:absolute;left:199px;top:240px;font-family:"Arimo",Arial,sans-serif;font-size:9px;letter-spacing:1px}
.chat{position:absolute;left:886px;top:253px;width:156px;height:36px;background:var(--red);display:flex;align-items:center;justify-content:center;gap:10px;font-family:"Arimo",Arial,sans-serif;font-size:14px}
</style>
</head>
<body>

<header class="site-header">
  <div class="brand"><span class="brand-dot"></span><span class="brand-name">Brevonix</span></div>
  <nav class="main-nav">
    <span class="active">HOME</span><span>ABOUT</span><span>WHY BREVONIX</span><span>FEATURES</span><span>ADVANTAGES</span><span>BEST OF CLASS HARDWARE</span><span>SUPPORT</span><span>CONTACT</span>
  </nav>
  <div class="social-top"><i></i><i></i><i></i></div>
</header>

<section class="hero" role="img" aria-label="Red digital world map with network nodes and people icons">
  <div class="hero-mark"><i></i><b>Brevonix</b></div>
  <h1 class="hero-title">INVENIENT VERITATEM</h1>
  <p class="hero-sub">BREVONIX UNIVERSAL COMMUNICATION</p>
  <span class="btn-outline">LEARN MORE</span>
</section>

<section class="about">
  <h2 class="section-title">ABOUT US</h2>
  <p>Brevonix Universal Communication was born out f the desire to offer reliable, affordable phone systems for the small- to medium-sized business. Since 2003, we have offered hosted VOIP PBX and call routing services, but they were bundled with larger IT services. As such, it was only cost-effective for the large corporate client.</p>
  <span class="btn-outline">LEARN MORE</span>
</section>
<svg class="notch" style="top:621px" viewBox="0 0 60 30"><polygon points="0,0 60,0 30,30" fill="#6a0000"/><polyline points="22,6 30,12 38,6" fill="none" stroke="#fff" stroke-width="1.5"/></svg>

<section class="why">
  <svg class="why-photo" viewBox="0 0 1200 551" role="img" aria-label="Woman touching a glowing network interface with wireless icons">
    <defs><linearGradient id="whyGrad" x1="0" y1="0" x2="1" y2="1"><stop offset="0" stop-color="#0c1a2e"/><stop offset=".55" stop-color="#3a5a7c"/><stop offset="1" stop-color="#10223a"/></linearGradient></defs>
    <polygon points="602,0 1200,0 1200,551 663,551" fill="url(#whyGrad)"/>
  </svg>
  <h2 class="section-title">WHY BREVONIX</h2>
  <p class="why-kicker">BREVONIX UNIVERSAL COMMUNICATION</p>
  <div class="why-copy">
    <p>Fax, Phone, Wireless, Email, Text Messaging, Web, Cellular, and Integrated Backoffice Systems.</p>
    <p>In addition to being costly, traditional communication systems tend to operate in isolated modes leaving little room for easy integration. In addition to delivering a best-of-class feature PBX set, our solution enables our clients to:</p>
  </div>
  <ul class="why-list">
    <li><svg width="16" height="12" viewBox="0 0 16 12"><path d="M1 4a10 10 0 0 1 14 0M3.5 6.5a6.5 6.5 0 0 1 9 0M6 9a3 3 0 0 1 4 0" fill="none" stroke="#333" stroke-width="1.6"/><circle cx="8" cy="11" r="1" fill="#333"/></svg>Define their own requirements based on their style and needs. We do not impose a predefined structure.</li>
    <li><svg width="16" height="12" viewBox="0 0 16 12"><path d="M1 4a10 10 0 0 1 14 0M3.5 6.5a6.5 6.5 0 0 1 9 0M6 9a3 3 0 0 1 4 0" fill="none" stroke="#333" stroke-width="1.6"/><circle cx="8" cy="11" r="1" fill="#333"/></svg>Seamlessly Integrate many locations into a unified infrastructure.</li>
    <li><svg width="16" height="12" viewBox="0 0 16 12"><path d="M1 4a10 10 0 0 1 14 0M3.5 6.5a6.5 6.5 0 0 1 9 0M6 9a3 3 0 0 1 4 0" fill="none" stroke="#333" stroke-width="1.6"/><circle cx="8" cy="11" r="1" fill="#333"/></svg>Eliminate cost of hardware purchases. When you use our service, the hardware is a standard part of the offering and provided on use only basis.</li>
    <li><svg width="16" height="12" viewBox="0 0 16 12"><path d="M1 4a10 10 0 0 1 14 0M3.5 6.5a6.5 6.5 0 0 1 9 0M6 9a3 3 0 0 1 4 0" fill="none" stroke="#333" stroke-width="1.6"/><circle cx="8" cy="11" r="1" fill="#333"/></svg>Integrate a wide array of special features as well as defined feature sets.</li>
  </ul>
  <span class="btn-outline">LEARN MORE</span>
</section>
<svg class="notch" style="top:943px" viewBox="0 0 60 30"><polygon points="0,0 60,0 30,30" fill="#eee"/><polyline points="22,6 30,12 38,6" fill="none" stroke="#999" stroke-width="1.5"/></svg>

<section class="benefits">
  <h2 class="section-title">BENEFITS</h2>
  <p class="benefits-sub">DISCOVERING YOUR NEEDS, CREATING SOLUTIONS THAT TRULY WORK</p>
  <div class="benefit featured" style="left:133px;top:134px"><svg width="22" height="16" viewBox="0 0 16 12"><path d="M1 4a10 10 0 0 1 14 0M3.5 6.5a6.5 6.5 0 0 1 9 0M6 9a3 3 0 0 1 4 0" fill="none" stroke="#fff" stroke-width="1.6"/><circle cx="8" cy="11" r="1" fill="#fff"/></svg><h3>QUICK ROI</h3><p>Equipment is included in the service</p></div>
  <div class="benefit" style="left:450px;top:134px"><svg width="22" height="16" viewBox="0 0 16 12"><path d="M1 4a10 10 0 0 1 14 0M3.5 6.5a6.5 6.5 0 0 1 9 0M6 9a3 3 0 0 1 4 0" fill="none" stroke="#fff" stroke-width="1.6"/><circle cx="8" cy="11" r="1" fill="#fff"/></svg><h3>SECURE</h3><p>Encrypted lines</p></div>
  <div class="benefit" style="left:767px;top:134px"><svg width="22" height="16" viewBox="0 0 16 12"><path d="M1 4a10 10 0 0 1 14 0M3.5 6.5a6.5 6.5 0 0 1 9 0M6 9a3 3 0 0 1 4 0" fill="none" stroke="#fff" stroke-width="1.6"/><circle cx="8" cy="11" r="1" fill="#fff"/></svg><h3>EASY INSTALLATION</h3><p>Very little business interrup-tion</p></div>
  <div class="benefit" style="left:133px;top:280px"><svg width="22" height="16" viewBox="0 0 16 12"><path d="M1 4a10 10 0 0 1 14 0M3.5 6.5a6.5 6.5 0 0 1 9 0M6 9a3 3 0 0 1 4 0" fill="none" stroke="#fff" stroke-width="1.6"/><circle cx="8" cy="11" r="1" fill="#fff"/></svg><h3>EXPANDABLE</h3><p>One unit at a time</p></div>
  <div class="benefit" style="left:450px;top:280px"><svg width="22" height="16" viewBox="0 0 16 12"><path d="M1 4a10 10 0 0 1 14 0M3.5 6.5a6.5 6.5 0 0 1 9 0M6 9a3 3 0 0 1 4 0" fill="none" stroke="#fff" stroke-width="1.6"/><circle cx="8" cy="11" r="1" fill="#fff"/></svg><h3>INTUITIVE</h3><p>Easy to learn and run</p></div>
  <div class="benefit" style="left:767px;top:280px"><svg width="22" height="16" viewBox="0 0 16 12"><path d="M1 4a10 10 0 0 1 14 0M3.5 6.5a6.5 6.5 0 0 1 9 0M6 9a3 3 0 0 1 4 0" fill="none" stroke="#fff" stroke-width="1.6"/><circle cx="8" cy="11" r="1" fill="#fff"/></svg><h3>FAIL-OVER</h3><p>Calls go through even if a supplier phone company has outages</p></div>
</section>
<div class="dashes"><i></i><i></i><i></i></div>
<svg class="notch" style="top:1958px" viewBox="0 0 60 30"><polygon points="0,0 60,0 30,30" fill="#b00000"/><polyline points="22,6 30,12 38,6" fill="none" stroke="#fff" stroke-width="1.5"/></svg>

<section class="newsletter">
  <h2>NEWSLETTER SUBSCRIBE</h2>
  <span class="rule"></span>
  <small>Join our Email list</small>
  <div class="email-field"><span>Enter Email Id</span><svg width="12" height="9" viewBox="0 0 12 9"><rect x=".5" y=".5" width="11" height="8" fill="#bbb"/><polyline points="1,1 6,5 11,1" fill="none" stroke="#fff"/></svg></div>
  <div class="subscribe">Subscribe</div>
</section>

<footer class="site-footer">
  <div class="foot-brand"><i></i><b>Brevonix</b></div>
  <p class="foot-about">Duis aute irure dolor in reprehenderit in voluptate velit esse cillum dolore eu fugiat nulla pariatur. Excepteur sint occaecat cupi-datat non proident</p>
  <div class="foot-col quick"><h4>Quick Links</h4><ul><li>Home</li><li>About Us</li><li>Why Brevonix</li><li>Features</li><li>Advantages</li><li>Best of class hardware</li><li>Support</li><li>Contact</li></ul></div>
  <div class="foot-col testimonial"><h4>Testimonials</h4><p>" Duis aute irure dolor in reprehenderit in voluptate velit esse cillum dolore eu fugiat nulla pariatur. Excepteur sint occaecat cupi-datat non proident "</p><cite>- Marisa</cite></div>
  <div class="foot-col contact"><h4>Contact</h4><ul><li><i></i>48 Harbor Lane, 10th Floor</li><li><i></i>+1-555-014-2678</li><li><i></i>info@brevonix.com</li><li><i></i>www.brevonix.com</li></ul></div>
  <div class="foot-social"><i></i><i></i><i></i><i></i><i></i><i></i></div>
  <p class="copyright">© 2018 WWW.BREVONIX.COM</p>
  <div class="chat"><svg width="18" height="14" viewBox="0 0 18 14"><path d="M1 1h12v8H6l-3 3V9H1z" fill="#fff"/></svg>Chat Online</div>
</footer>
<svg class="notch" style="top:2150px" viewBox="0 0 60 30"><polygon points="0,0 60,0 30,30" fill="#ececec"/><polyline points="22,6 30,12 38,6" fill="none" stroke="#999" stroke-width="1.5"/></svg>

</body>
</html>
```